KBT Business Cards

We require business cards for our business. We would like a matte black back to the card, with our logo centred in the middle. The front side of the card is open to design.

Target Market(s)

Clients looking for legal services (professional)

Industry/Entity Type

Legal

Contact Information for Business Card

Doran Kelbrath
Partner
Mobile: 0461 738 524
Email: doran@kbtlaw.co
Website: www.kbtlaw.co
Level 3, 118 Wendmore Street
Sydney NSW 2000

Font styles to use
Other font styles liked:
• Avenir

Colors
f04a50
ffffff
1b1b1b

Requirements
Must have
• Black back with logo included in the centre of the card.
• Our font is Avenir.

```html
<!DOCTYPE html>
<html lang="en">
<head>
<meta charset="utf-8">
<title>KBT Business Cards</title>
<link rel="stylesheet" href="https://fonts.googleapis.com/css2?family=Nunito+Sans:wght@400;600;700&display=swap">
<style>
  :root {
    --card-black: #1b1b1b;
    --crimson: #a8183c;
    --white: #ffffff;
    --muted: #cfcfcf;
    --backdrop: #c9c9c7;
  }
  * { box-sizing: border-box; margin: 0; padding: 0; }
  html, body { width: 1200px; height: 675px; overflow: hidden; }
  body {
    background: var(--backdrop);
    font-family: "Nunito Sans", Arial, sans-serif;
    color: var(--white);
    position: relative;
  }
  .card {
    position: absolute;
    top: 189px;
    width: 520px;
    height: 297px;
    border-radius: 18px;
    background: var(--card-black);
    overflow: hidden;
  }
  .card-front { left: 60px; }
  .card-back { left: 620px; }

  .brand { display: flex; align-items: flex-start; gap: 12px; }
  .brand-square {
    width: 30px; height: 30px;
    background: var(--crimson);
    flex: none;
    margin-top: 3px;
  }
  .brand-name {
    font-weight: 700;
    font-size: 15px;
    line-height: 1.05;
    letter-spacing: 0.5px;
    text-transform: uppercase;
    color: var(--white);
  }

  .card-front .brand { position: absolute; left: 34px; top: 30px; }
  .holder { position: absolute; left: 34px; top: 120px; }
  .holder-name { font-size: 17px; font-weight: 600; letter-spacing: 0.6px; text-transform: uppercase; }
  .holder-role { font-size: 12.5px; color: var(--muted); margin-top: 1px; }

  .contact-list {
    position: absolute; left: 34px; top: 182px;
    list-style: none;
    font-size: 13.5px; letter-spacing: 0.4px; line-height: 17px;
  }
  .contact-list li { display: flex; align-items: center; gap: 9px; }
  .contact-icon { width: 10px; height: 10px; flex: none; }
  .divider {
    position: absolute; left: 34px; right: 70px; top: 240px;
    height: 1px; background: var(--crimson);
  }
  .address {
    position: absolute; right: 34px; top: 252px;
    text-align: right; font-size: 13.5px; line-height: 17px; letter-spacing: 0.3px;
  }

  .back-waves { position: absolute; inset: 0; }
  .card-back .brand { position: absolute; left: 200px; top: 102px; }
  .back-web {
    position: absolute; right: 38px; bottom: 26px;
    font-size: 13px; font-weight: 600; letter-spacing: 0.6px;
  }
</style>
</head>
<body>

  <section class="card card-front" aria-label="Business card front">
    <div class="brand">
      <span class="brand-square"></span>
      <p class="brand-name">Kelbrath<br>Brandt<br>Tolle</p>
    </div>

    <div class="holder">
      <p class="holder-name">Doran Kelbrath</p>
      <p class="holder-role">Partner</p>
    </div>

    <ul class="contact-list">
      <li>
        <svg class="contact-icon" viewBox="0 0 10 10" aria-hidden="true"><path d="M2 0.5 L3.8 2.6 L2.8 3.8 Q4 6 6.2 7.2 L7.4 6.2 L9.5 8 L8.2 9.5 Q3.5 9 0.5 1.8 Z" fill="var(--crimson)"/></svg>
        0461 738 524
      </li>
      <li>
        <svg class="contact-icon" viewBox="0 0 10 10" aria-hidden="true"><rect x="0.6" y="2" width="8.8" height="6.2" fill="none" stroke="var(--crimson)" stroke-width="1.2"/><path d="M0.8 2.3 L5 5.6 L9.2 2.3" fill="none" stroke="var(--crimson)" stroke-width="1.1"/></svg>
        doran@kbtlaw.co
      </li>
      <li>
        <svg class="contact-icon" viewBox="0 0 10 10" aria-hidden="true"><circle cx="5" cy="5" r="4.3" fill="none" stroke="var(--crimson)" stroke-width="1.1"/><ellipse cx="5" cy="5" rx="1.8" ry="4.3" fill="none" stroke="var(--crimson)" stroke-width="0.9"/><line x1="0.7" y1="5" x2="9.3" y2="5" stroke="var(--crimson)" stroke-width="0.9"/></svg>
        www.kbtlaw.co
      </li>
    </ul>

    <div class="divider"></div>

    <p class="address">Level 3, 118 Wendmore Street<br>Sydney NSW 2000</p>
  </section>

  <section class="card card-back" aria-label="Business card back">
    <svg class="back-waves" viewBox="0 0 520 297" preserveAspectRatio="none" aria-hidden="true">
      <path d="M0 48 C70 120 150 175 260 205 C350 228 440 234 520 234 L520 297 L0 297 Z" fill="var(--crimson)"/>
      <path d="M0 0 L46 0 C80 52 130 98 200 130 C125 110 60 72 0 30 Z" fill="var(--white)"/>
    </svg>
    <div class="brand">
      <span class="brand-square"></span>
      <p class="brand-name">Kelbrath<br>Brandt<br>Tolle</p>
    </div>
    <p class="back-web">www.kbtlaw.co</p>
  </section>

</body>
</html>
```